Business Card and Simple Logo Desgin

New Zealand based start up company "Vesta Advisory LTD" requires business cards and simple logo design.

Card Content.

Vesta Advisory LTD

Rebecca Thornbury
CA, BMS (Hons)

r.thornbury@vestaadvisory.co.nz
PH +64 21 574 613

Target Market(s)

Corporate Business in IT, Finance and accounting.

Industry/Entity Type

Business

```html
<!DOCTYPE html>
<html lang="en">
<head>
<meta charset="utf-8">
<title>Vesta Advisory LTD – Business Card</title>
<link rel="stylesheet" href="https://fonts.googleapis.com/css2?family=Ubuntu:wght@400;500;700&display=swap">
<style>
  :root {
    --card-bg: #000000;
    --card-edge: #8a8a8a;
    --ink: #ffffff;
    --mark-grey: #d6d6d6;
    --band-green: #66ff1a;
    --band-blue: #0033ff;
    --band-orange: #ff9900;
    --band-red: #ff0033;
  }
  * { margin: 0; padding: 0; box-sizing: border-box; }
  html, body {
    width: 1200px;
    height: 696px;
    overflow: hidden;
    background: var(--card-bg);
  }
  .business-card {
    position: relative;
    width: 1200px;
    height: 696px;
    background: var(--card-bg);
    border: 2px solid var(--card-edge);
    color: var(--ink);
    font-family: "Ubuntu", sans-serif;
  }
  .brand {
    position: absolute;
    left: 93px;
    top: 114px;
    display: flex;
    align-items: center;
    gap: 28px;
  }
  .brand-dot {
    width: 96px;
    height: 96px;
    border-radius: 50%;
    background: var(--mark-grey);
  }
  .brand-name {
    font-family: "Ubuntu", sans-serif;
    font-weight: 500;
    font-size: 46px;
    line-height: 1;
    letter-spacing: 0.5px;
    color: var(--ink);
  }
  .contact-line {
    position: absolute;
    left: 93px;
    line-height: 1;
    white-space: nowrap;
  }
  .person-name { top: 331px; font-size: 34px; font-weight: 700; }
  .credentials { top: 378px; font-size: 33px; font-weight: 400; }
  .email       { top: 479px; font-size: 31px; font-weight: 400; }
  .phone       { top: 531px; font-size: 31px; font-weight: 400; }
  .colour-band {
    position: absolute;
    left: 93px;
    top: 637px;
    width: 1036px;
    height: 10px;
    display: flex;
  }
  .colour-band span { display: block; height: 100%; }
  .band-green  { width: 261px; background: var(--band-green); }
  .band-blue   { width: 260px; background: var(--band-blue); }
  .band-orange { width: 255px; background: var(--band-orange); }
  .band-red    { width: 260px; background: var(--band-red); }
</style>
</head>
<body>
  <main class="business-card">
    <header class="brand">
      <div class="brand-dot" aria-hidden="true"></div>
      <h1 class="brand-name">Vesta Advisory LTD</h1>
    </header>

    <p class="contact-line person-name">Rebecca Thornbury</p>
    <p class="contact-line credentials">CA, BMS (Hons)</p>
    <p class="contact-line email">r.thornbury@vestaadvisory.co.nz</p>
    <p class="contact-line phone">PH +64 21 574 613</p>

    <div class="colour-band" aria-hidden="true">
      <span class="band-green"></span>
      <span class="band-blue"></span>
      <span class="band-orange"></span>
      <span class="band-red"></span>
    </div>
  </main>
</body>
</html>
```